Business Card Design

Electronic Security
Alarm Systems
CCTV
Electronic Access Control
Security System Integration

Industry/Entity Type

Business

Contact Information for Business Card

Gareth Linwood
PO Box 862
Ashgrove Qld 4071
Phone 07 38526147
Mob 0427395816

```html
<!DOCTYPE html>
<html lang="en">
<head>
<meta charset="utf-8">
<title>Business Card – Gareth Linwood</title>
<link rel="stylesheet" href="https://fonts.googleapis.com/css2?family=Montserrat:wght@400;600&display=swap">
<style>
  :root {
    --backdrop: #e6e4e1;
    --card-black: #0c0c0c;
    --card-white: #ffffff;
    --accent-orange: #f08a1c;
    --accent-yellow: #f6c816;
    --text-light: #f4f4f4;
    --text-dark: #2a2a2a;
  }
  * { margin: 0; padding: 0; box-sizing: border-box; }
  html, body { width: 1200px; height: 848px; overflow: hidden; }
  body {
    background: var(--backdrop);
    font-family: "Montserrat", Arial, sans-serif;
    position: relative;
  }
  .business-card {
    position: absolute;
    left: 150px;
    top: 169px;
    width: 900px;
    height: 510px;
    border-radius: 34px;
    overflow: hidden;
    background: var(--card-black);
    box-shadow: 0 18px 40px rgba(0,0,0,0.25);
  }
  .card-shapes { position: absolute; inset: 0; }
  .holder-name {
    position: absolute;
    left: 62px;
    top: 62px;
    color: var(--text-light);
    font-weight: 600;
    font-size: 27px;
    letter-spacing: 0.5px;
  }
  .contact-list {
    position: absolute;
    left: 62px;
    top: 318px;
    list-style: none;
    color: var(--text-light);
    font-weight: 400;
    font-size: 24px;
    line-height: 34px;
    letter-spacing: 0.5px;
  }
  .contact-list li { display: flex; align-items: center; gap: 16px; }
  .contact-list .icon { width: 22px; height: 22px; flex: none; }
  .contact-list .indent { padding-left: 38px; }
  .brand-name {
    position: absolute;
    left: 500px;
    top: 222px;
    width: 360px;
    color: var(--text-dark);
    font-weight: 600;
    font-size: 36px;
    line-height: 44px;
    letter-spacing: 1px;
  }
</style>
</head>
<body>
  <div class="business-card">
    <svg class="card-shapes" viewBox="0 0 900 510" aria-hidden="true">
      <defs>
        <linearGradient id="edge-glow" x1="0" y1="0" x2="0" y2="1">
          <stop offset="0" stop-color="#f6c816"/>
          <stop offset="0.5" stop-color="#f08a1c"/>
          <stop offset="1" stop-color="#f6c816"/>
        </linearGradient>
      </defs>
      <circle class="accent-arc" cx="893" cy="255" r="525" fill="url(#edge-glow)"/>
      <circle class="white-panel" cx="900" cy="255" r="520" fill="#ffffff"/>
    </svg>

    <p class="holder-name">Gareth Linwood</p>

    <ul class="contact-list">
      <li>
        <svg class="icon" viewBox="0 0 22 22" aria-hidden="true">
          <rect x="5" y="2" width="12" height="18" rx="2.5" fill="none" stroke="#f6c816" stroke-width="2.4"/>
        </svg>
        0427395816
      </li>
      <li>
        <svg class="icon" viewBox="0 0 22 22" aria-hidden="true">
          <path d="M6 3 L9 7 L7 9 C8 12 10 14 13 15 L15 13 L19 16 L17 19 C10 19 3 12 3 5 Z" fill="#f6c816"/>
        </svg>
        07 38526147
      </li>
      <li>
        <svg class="icon" viewBox="0 0 22 22" aria-hidden="true">
          <path d="M11 2 C6.5 2 4 5 4 8.5 C4 13 11 20 11 20 C11 20 18 13 18 8.5 C18 5 15.5 2 11 2 Z" fill="#f6c816"/>
          <circle cx="11" cy="8.5" r="2.6" fill="#0c0c0c"/>
        </svg>
        PO Box 862 Ashgrove
      </li>
      <li class="indent">Qld 4071</li>
    </ul>

    <p class="brand-name">Kestrel Alarm Systems</p>
  </div>
</body>
</html>
```